KRT Engineering Business Card Design

We’re looking for an elegant, clean, and timeless business card design that communicates experience, capability, and reliability.

KRT Engineering was established in 1995 , we are a Government Contracting company providing Professional Services to the Office of Frontier Affairs, Harbor Protection and the Vantage Collective. Our capabilities include: Acquisition & Program Management; Intelligence & Security Operations; Cyber, IT & Network Operations; Lifecycle Logistics & Asset Readiness; C5ISR Systems Engineering & Sustainment.

We want the card to reflect a straightforward, confident approach to business. The design should feel polished and professional without being flashy or overly corporate.

Design Direction
Clean, sophisticated, and uncluttered
Elegant but understated
Strong typography and thoughtful spacing
A timeless aesthetic rather than something overly trendy
Confident and established, with a sense of substance
Easy to read and practical in a real-world business setting

The overall impression should be: “These are experienced professionals who know what they’re doing, do what they say, and can be relied upon.”

We’re open to creative interpretations. The finished card should feel distinctive through its typography, proportions, layout, and attention to detail rather than through excessive graphics or visual effects.

We’re looking for a design that would make a potential client immediately feel that they’re dealing with a capable, trustworthy, and established company.

Company Colors: Navy and Gold/Yellow (but you do not need to use these colors on the card)
Company Name: KRT Engineering Associates, Inc. (known as KRT Engineering)
Website: krtengineering.com
Company Logo: Navy & Gold (other variations attached)

```html
<!DOCTYPE html>
<html lang="en">
<head>
<meta charset="utf-8">
<title>KRT Engineering Business Card</title>
<link rel="stylesheet" href="https://fonts.googleapis.com/css2?family=Arimo:wght@700&family=Poppins:wght@400&display=swap">
<style>
  :root {
    --stage: #5f5f5f;
    --navy-deep: #1f2554;
    --navy: #29306a;
    --navy-mid: #2e3670;
    --navy-light: #41528a;
    --dusk: #62628a;
    --mark-front: #1d2252;
    --gold: #f6dd4a;
    --white: #ffffff;
    --ink-light: #eef0f7;
  }
  * { margin: 0; padding: 0; box-sizing: border-box; }
  html, body { width: 900px; height: 1200px; overflow: hidden; }
  body { background: var(--stage); position: relative; font-family: "Poppins", sans-serif; }

  .card { position: absolute; left: 136px; width: 630px; height: 363px; overflow: hidden; }

  .card-front {
    top: 214px;
    background: linear-gradient(135deg, var(--navy) 0%, var(--navy-mid) 100%);
    display: flex; align-items: center; justify-content: center;
  }
  .card-front .wordmark {
    font-family: "Arimo", sans-serif; font-weight: 700;
    font-size: 104px; letter-spacing: -3px; line-height: 1;
    color: var(--mark-front);
  }

  .card-back {
    top: 629px;
    background: linear-gradient(100deg, var(--navy-deep) 0%, var(--navy-deep) 35%, #2c3468 60%, var(--navy-light) 100%);
  }
  .card-back .photo-area {
    position: absolute; right: 0; top: 0; width: 440px; height: 100%;
    background: linear-gradient(160deg, rgba(72,92,148,0.7) 0%, rgba(58,70,118,0.5) 45%, var(--dusk) 100%);
    -webkit-mask-image: linear-gradient(to right, transparent 0%, rgba(0,0,0,0.5) 30%, #000 60%);
    mask-image: linear-gradient(to right, transparent 0%, rgba(0,0,0,0.5) 30%, #000 60%);
  }
  .card-back .wordmark {
    position: absolute; left: 355px; top: 158px;
    font-family: "Arimo", sans-serif; font-weight: 700;
    font-size: 88px; letter-spacing: -3px; line-height: 1;
    color: var(--white);
  }

  .contact { position: absolute; left: 42px; top: 50px; color: var(--ink-light); }
  .contact .name {
    font-family: "Arimo", sans-serif; font-weight: 700;
    font-size: 25px; color: var(--white); line-height: 1.2;
  }
  .contact .role { font-size: 17px; margin-top: 2px; margin-left: 2px; letter-spacing: 0.7px; line-height: 1.3; }
  .contact .rule { width: 148px; height: 1px; background: var(--gold); margin: 9px 0 0 2px; }
  .contact .address {
    font-size: 16.5px; line-height: 25px; letter-spacing: 0.7px;
    margin: 9px 0 0 2px; font-style: normal;
  }
  .contact .rule.lower { margin-top: 9px; }
  .contact .links { list-style: none; margin-top: 11px; }
  .contact .links li {
    display: flex; align-items: center; gap: 8px;
    font-size: 17px; letter-spacing: 1.3px; line-height: 1; height: 29px;
  }
  .contact .links .icon { width: 14px; height: 14px; flex: none; margin-left: 3px; }
</style>
</head>
<body>

  <section class="card card-front" aria-label="Card front">
    <span class="wordmark">KRT</span>
  </section>

  <section class="card card-back" aria-label="Card back">
    <div class="photo-area" role="img" aria-label="Fighter jet banking through a blue sky"></div>
    <span class="wordmark">KRT</span>

    <div class="contact">
      <h1 class="name">Marla Venhurst, P.E.</h1>
      <p class="role">CEO &amp; President</p>
      <div class="rule"></div>
      <address class="address">
        4820 Harlow Avenue,<br>
        Suite 310, Bayport Heights,<br>
        VA 20199
      </address>
      <div class="rule lower"></div>
      <ul class="links">
        <li>
          <svg class="icon" viewBox="0 0 24 24" aria-hidden="true">
            <path fill="var(--gold)" d="M6.6 10.8a15.1 15.1 0 0 0 6.6 6.6l2.2-2.2a1 1 0 0 1 1-.25 11.4 11.4 0 0 0 3.6.57 1 1 0 0 1 1 1V20a1 1 0 0 1-1 1A17 17 0 0 1 3 4a1 1 0 0 1 1-1h3.5a1 1 0 0 1 1 1c0 1.25.2 2.45.57 3.57a1 1 0 0 1-.25 1z"/>
          </svg>
          555-301-7264
        </li>
        <li>
          <svg class="icon" viewBox="0 0 24 24" aria-hidden="true">
            <g fill="none" stroke="var(--gold)" stroke-width="2">
              <circle cx="12" cy="12" r="9"/>
              <ellipse cx="12" cy="12" rx="4" ry="9"/>
              <path d="M3 12h18M5 7h14M5 17h14"/>
            </g>
          </svg>
          krtengineering.com
        </li>
        <li>
          <svg class="icon" viewBox="0 0 24 24" aria-hidden="true">
            <circle cx="12" cy="12" r="10" fill="var(--gold)"/>
          </svg>
          krt-engineering-associates-inc
        </li>
      </ul>
    </div>
  </section>

</body>
</html>
```